Commercial Real Estate Corporate Site

Our company sells an ERP software to Commercial Real Estate Companies, this project is part of a marketing and sales relaunch of the company.

See attached for PDF formatted Design brief

The software is a modular system where client’s can adopt one module at a time. Our customers are corporate clients who own between 10M and 10B of real estate properties. The typical customer is from the IT or the Financial arm of the company. Our differentiation in the market is that our system is built on a no-code environment, so making changes for the client is quick. Incumbents in the market have long implementation cycles, and customization is often not possible. Competitors are Quorvel, TKB, PlotNest, Vumora.

We need a design for our site which will be implemented into Brevo Forge. **All designs must be compatible with the newest version of Brevo Forge.**

We have produced the following attached assets to use in the website design.:

1. Logo
2. Brand Guidelines
3. Content for Pages
4. Menu Structures
5. Illustrations (modules)
I can't attach them because the files are too big, so they're in this google drive instead:
https://files.examplestore.net/share/k29Xa7Lq0Pz3Rt8MwB5nYc4Hv1Jd6Fe?mode=view

The mechanic for our sales process is as follows:

1. We find on module from our application that a client is interested in. The illustrations that we’ve attached represent the individual modules (elements) of the software.
1. For instance, one of our current customers has purchased a commissions module from us which helps calculate the commission that brokers receive for buying and selling their properties.
2. We provide immense value through the module, and then keep in sales communication with the client to determine which other modules we can implement for them.
1. For instance, in the example above, the client is so happy with the commissions module that they want to start working with our leasing module as well. In the next business quarter, they also choose to add our financials module to their business systems.

### Logo

Attached

### Brand Guidelines

Attached

We are open to suggestions on the secondary colour palette.

### **Site Copy**

**We require the following pages to be created; For now, we will do one Market Page, one Product Page, and one Platform / Services Page, and we will use those as inspiration to create the other dozen Marketing Pages and 30 or so Product Pages.**

**Homepage**

Attached

**Market Page** - look at the quorvel site under the Office, Industrial, Retail (https://www.quorvel.com/products/quorvel-commercial-suite/)

**Product** - One product provided, but there will be 30 - look at the vumora page

(https://www.vumora.com/products/general-accounting)

**Platform / Services Page** - pages that tell the story of our platform and services, content to be provided - the platform will use our modules as it highlights the story of the configurability and composability of the platform. Instead of the icons that they use, we want to use our modules.

- https://www.pelbrix.com/enterprise-applications-platform
- https://www.pelbrix.com/cloud-architecture

**Team Page** - just add sample content for starters (6 Team Members to start)

**Schedule Demo Page** - the call to action for all pages

(https://go.vumora.com/schedule-demo.html)

### Menu Structure

The menu is provided as an attachment.

### Illustrations Information

A note about the illustrations - we have provided an illustrator file with the modules, and if you’d like you can arrange the in any way that you’d like to. We especially like when the modules are positioned like a periodic table of the elements.

Our existing clients are

- Torvane Coop - https://www.torvanecoop.com/real-estate/
- Dalsworth Realestate https://dalsworth.com

Our competitors are

- Quorvel - www.quorvel.com
- TKB - [www.tkbsoftware.com](https://www.tkbsoftware.com/) (we don’t like how this one looks)
- Vumora - www.vumora.com
- Plotnest - www.plotnest.com

Design inspiration

- https://lark-studio.brevosite.com/velmo
- Corporate
- Established
- Modern

### Stock Images Guidance

- https://www.drafta.net/design/QXR7Lm2TpWz/Hk9vN3c8Yd41-FbqsaZRr/edit?utm_content=QXR7Lm2TpWz&utm_campaign=designshare&utm_medium=link2&utm_source=sharebutton

Target Market(s)

Commercial Real Estate Companies - they typically own a portfolio of 50 - 5000 real estate properties and need a software to manage it all.

Coding

Coded - Design and coding required

Number of Pages Required

5+ page

Font styles to use
Other font styles liked:
• Fonts defined in brand guideline

Requirements
Must have
• Brevo Forge, Use the Elemental Design, Download ai.zip and png.zip Use Brand Guideline,
Nice to have
• Check design breif

```html
<!DOCTYPE html>
<html lang="en">
<head>
<meta charset="utf-8">
<title>Kavlen — Enterprise Applications Platform</title>
<link rel="stylesheet" href="https://fonts.googleapis.com/css2?family=Montserrat:wght@600;700;800&family=Roboto:wght@400;500;700&display=swap">
<style>
:root{
  --red:#e30b13;
  --red-bright:#f2292b;
  --ink:#222;
  --body:#555;
  --grey-bg:#f3f3f3;
  --dark:#161616;
  --white:#fff;
}
*{margin:0;padding:0;box-sizing:border-box}
html,body{width:1200px;height:3807px;overflow:hidden;background:var(--white)}
body{position:relative;font-family:"Roboto",Arial,sans-serif;color:var(--body);font-size:14.5px;line-height:20px}
.decor{position:absolute;left:0;top:0;width:1200px;height:3807px}
.abs{position:absolute}
h1,h2,h3,h4{font-family:"Montserrat",Arial,sans-serif;color:var(--ink)}
.rule{display:block;width:50px;height:2px;background:var(--red)}
.btn{display:inline-block;background:var(--red);color:var(--white);font-family:"Roboto",Arial,sans-serif;font-weight:700;font-size:13.5px;padding:0 21px;height:40px;line-height:40px;border-radius:3px;text-transform:uppercase;text-decoration:none}
p{text-align:justify;margin-bottom:20px}

.topbar{left:0;top:0;width:1200px;height:40px;background:var(--red);color:var(--white);font-size:13px;display:flex;justify-content:space-between;align-items:center;padding:0 143px}
.topbar span{display:flex;align-items:center;gap:9px}
.navbar{left:0;top:40px;width:1200px;height:75px;display:flex;align-items:center;justify-content:space-between;padding:0 143px;border-bottom:1px solid #eee;background:var(--white)}
.brand{font-family:"Montserrat",Arial,sans-serif;font-weight:800;font-size:32px;color:var(--red);letter-spacing:1px}
.menu{display:flex;gap:30px;font-size:13.5px;color:#333;height:75px;align-items:center}
.menu a{color:#333;text-decoration:none;height:75px;line-height:75px;position:relative}
.menu a.active{color:var(--red)}
.menu a.active::after{content:"";position:absolute;left:0;right:0;bottom:10px;height:3px;background:var(--red)}

.hero-card{left:121px;top:316px;width:396px;height:200px;background:rgba(25,25,25,.9);padding:18px 20px}
.hero-card h1{color:var(--white);font-size:50px;line-height:56px;font-weight:700;letter-spacing:1px}
.hero-card p{color:var(--white);font-size:14px;line-height:20px;margin:8px 2px 14px;text-align:left}
.hero-card .btn{margin-left:2px}
.arrow{width:38px;height:38px;border-radius:50%;background:var(--white);display:flex;align-items:center;justify-content:center;top:399px}

.eyebrow{color:var(--red);font-weight:600;font-size:14px;font-family:"Montserrat",Arial,sans-serif;letter-spacing:.3px}
.welcome{left:598px;top:940px;width:457px}
.welcome h2{font-size:36px;line-height:44px;margin:2px 0 10px}
.welcome .rule{margin-bottom:18px}

.about-head{left:0;top:1530px;width:1200px;text-align:center}
.about-head h2{font-size:36px;line-height:46px}
.about-head .rule{margin:6px auto 14px}
.about-head .eyebrow{font-size:15px}
.about-text{left:142px;top:1632px;width:458px}
.about-text h3{font-size:33px;line-height:42px;font-weight:600;margin-bottom:10px}

.modules{left:254px;top:2250px;width:690px;text-align:center;color:var(--white)}
.modules h2{color:var(--white);font-size:35px;line-height:46px}
.modules .rule{background:var(--white);margin:8px auto 26px}
.modules h4{color:var(--white);font-size:15px;margin-bottom:12px}
.modules p{text-align:center;color:var(--white);font-size:13.5px;line-height:20px}

.platform{left:598px;top:2855px;width:457px}
.platform h2{font-size:36px;line-height:46px}
.platform .rule{margin:4px 0 14px}
.platform .eyebrow{font-size:15px;line-height:20px;margin-bottom:12px}

.footer-col{top:3530px;color:#ddd}
.footer-col h4{color:var(--white);font-size:19px;line-height:26px;margin-bottom:10px}
.footer-col .rule{width:50px;margin-bottom:20px}
.footer-col p{font-size:13.5px;line-height:20px;color:#eee}
.links{display:grid;grid-template-columns:104px 100px;font-size:13.5px;line-height:20px;color:#eee}
.contact li{list-style:none;display:flex;gap:14px;font-size:13.5px;line-height:20px;color:#eee;margin-bottom:20px}
.contact svg{flex:none;margin-top:3px}
.footer-line{left:142px;top:3727px;width:913px;height:1px;background:#3a3a3a}
.copyright{left:0;top:3758px;width:1200px;text-align:center;color:#eee;font-size:13px}
</style>
</head>
<body>

<svg class="decor" viewBox="0 0 1200 3807" aria-hidden="false">
  <defs>
    <linearGradient id="heroTone" x1="0" y1="0" x2="1" y2="1">
      <stop offset="0" stop-color="#5f6873"/>
      <stop offset=".45" stop-color="#c9ced4"/>
      <stop offset=".75" stop-color="#e9ecef"/>
      <stop offset="1" stop-color="#7b8591"/>
    </linearGradient>
    <linearGradient id="archTone" x1="0" y1="0" x2="1" y2="1">
      <stop offset="0" stop-color="#dfe3e6"/><stop offset="1" stop-color="#8f98a0"/>
    </linearGradient>
    <linearGradient id="redBand" x1="0" y1="0" x2="0" y2="1">
      <stop offset="0" stop-color="#f5262a"/><stop offset="1" stop-color="#e01418"/>
    </linearGradient>
    <linearGradient id="tableTone" x1="0" y1="0" x2="1" y2="1">
      <stop offset="0" stop-color="#f1f2f2"/><stop offset=".5" stop-color="#dfe6e4"/><stop offset="1" stop-color="#eceeee"/>
    </linearGradient>
    <linearGradient id="platTone" x1="0" y1="0" x2="1" y2="0">
      <stop offset="0" stop-color="#6f6f6f"/><stop offset=".5" stop-color="#c9c9c9"/>
      <stop offset=".5" stop-color="#ff5a5a"/><stop offset="1" stop-color="#e21a1a"/>
    </linearGradient>
    <linearGradient id="footTone" x1="0" y1="0" x2="1" y2="1">
      <stop offset="0" stop-color="#222"/><stop offset="1" stop-color="#0e0e0e"/>
    </linearGradient>
    <linearGradient id="portraitTone" x1="0" y1="0" x2="1" y2="1">
      <stop offset="0" stop-color="#a9b7b0"/><stop offset=".5" stop-color="#e8e4df"/><stop offset="1" stop-color="#8c9a98"/>
    </linearGradient>
  </defs>

  <g role="img" aria-label="Hero photo: modern white architectural atrium with steel columns">
    <polygon points="0,115 1200,115 1200,650 600,828 0,650" fill="url(#heroTone)"/>
  </g>
  <polygon points="148,706 600,850 1050,706 600,822" fill="var(--red)"/>

  <g class="hex-cluster">
    <polygon points="338,929 436,985.5 436,1098.5 338,1155 240,1098.5 240,985.5" fill="var(--red)"/>
    <polygon points="240,1097 338,1153.5 338,1266.5 240,1323 142,1266.5 142,1153.5" fill="var(--red)"/>
    <polygon points="436,1097 534,1153.5 534,1266.5 436,1323 338,1266.5 338,1153.5" fill="var(--red)"/>
    <polygon role="img" aria-label="Photo: curved white building facade" points="338,952 416,997 416,1087 338,1132 260,1087 260,997" fill="url(#archTone)"/>
    <polygon role="img" aria-label="Photo: ribbed ceiling with round skylights" points="240,1120 318,1165 318,1255 240,1300 162,1255 162,1165" fill="#b9b0a3"/>
    <polygon role="img" aria-label="Photo: angular modern building against blue sky" points="436,1120 514,1165 514,1255 436,1300 358,1255 358,1165" fill="#a6b8cc"/>
  </g>

  <rect x="0" y="1431" width="1200" height="870" fill="var(--grey-bg)"/>
  <rect role="img" aria-label="Photo: smiling businesswoman holding glasses" x="630" y="1639" width="425" height="377" fill="url(#portraitTone)"/>

  <polygon points="148,2247 600,2106 1050,2247 600,2128" fill="var(--red)"/>
  <polygon points="0,2298 600,2136 1200,2298 1200,2638 0,2638" fill="url(#redBand)"/>
  <rect role="img" aria-label="Illustration: modules arranged as a periodic table of elements" x="381" y="2496" width="438" height="269" fill="url(#tableTone)"/>

  <polygon role="img" aria-label="Photo: curved metal architecture in grey and red" points="143,2860 248,2816 557,2870 557,3160 452,3254 143,3205" fill="url(#platTone)"/>

  <polygon points="148,3458 600,3318 1050,3458 600,3340" fill="var(--red)"/>
  <polygon points="0,3503 600,3337 1200,3503 1200,3807 0,3807" fill="url(#footTone)"/>
</svg>

<header>
  <div class="abs topbar">
    <span><svg width="13" height="10" viewBox="0 0 13 10"><rect width="13" height="10" rx="1" fill="#fff"/><path d="M0 0l6.5 5L13 0" stroke="#e30b13" fill="none"/></svg>Email : info@companyname.com</span>
    <span><svg width="12" height="12" viewBox="0 0 24 24"><path fill="#fff" d="M6.6 10.8a15 15 0 006.6 6.6l2.2-2.2c.3-.3.7-.4 1-.2 1.1.4 2.3.6 3.6.6.6 0 1 .4 1 1V20c0 .6-.4 1-1 1A17 17 0 013 4c0-.6.4-1 1-1h3.5c.6 0 1 .4 1 1 0 1.3.2 2.5.6 3.6.1.3 0 .7-.2 1z"/></svg>Call Us : +1 888 888 8888</span>
  </div>
  <nav class="abs navbar">
    <div class="brand">KAVLEN</div>
    <div class="menu">
      <a class="active">Home</a><a>Markets</a><a>Products</a><a>Platform</a><a>Services</a><a>Resources</a><a>About</a><a>Contact Us</a>
    </div>
  </nav>
</header>

<section class="hero">
  <div class="abs hero-card">
    <h1>ELEMENTAL</h1>
    <p>Kavlen is the real estate industry's modern alternative to rigid, legacy ERP systems.</p>
    <a class="btn">Get Started</a>
  </div>
  <div class="abs arrow" style="left:49px"><svg width="12" height="12" viewBox="0 0 12 12"><path d="M8 1L3 6l5 5" stroke="#222" stroke-width="1.8" fill="none"/></svg></div>
  <div class="abs arrow" style="left:1112px"><svg width="12" height="12" viewBox="0 0 12 12"><path d="M4 1l5 5-5 5" stroke="#222" stroke-width="1.8" fill="none"/></svg></div>
</section>

<section class="abs welcome">
  <div class="eyebrow">WELCOME TO</div>
  <h2>KAVLEN</h2>
  <span class="rule"></span>
  <p>An infinitely composable Enterprise Applications Platform (EAP) for real estate.</p>
  <p>Far beyond what's possible with tired, legacy real estate ERP software, Kavlen offers a complete industry solution, architected as flexible modules that can be assembled and configured into an infinite combination of processes and workflows.</p>
  <p>The Kavlen Enterprise solution seamlessly delivers both modular software and bundled services to transform your business with less risk, greater security, and lower cost.</p>
  <a class="btn">Learn More</a>
</section>

<section>
  <div class="abs about-head">
    <h2>ABOUT</h2>
    <span class="rule"></span>
    <div class="eyebrow">ONE SOLUTION - INFINITE POSSIBILITIES</div>
  </div>
  <div class="abs about-text">
    <h3>Kavlen Enterprise</h3>
    <p>Kavlen was born from decades of real estate enterprise software development and implementation experience — spanning hundreds of blue chip global real estate investment firms. But Kavlen is unlike anything you've experienced before.</p>
    <p>No more multi-million-dollar disruptive implementations. No more waiting for upgrades and enhancements that never come. No more trailing projects and disappointing customizations. No more settling for less than exactly what you want.</p>
    <p>You can begin using Kavlen simply — starting with a single module. Then, you can build-on with additional modules at your own pace. Kavlen Enterprise combines software and services in a simple, annual subscription.</p>
    <a class="btn">Learn More</a>
  </div>
</section>

<section class="abs modules">
  <h2>THE MODULES OF KAVLEN</h2>
  <span class="rule"></span>
  <h4>SIMPLE - SECURE - SCALABLE</h4>
  <p>Kavlen is the real estate industry's only infinitely composable Enterprise Applications Platform (EAP), ensuring scalability, security, auditability, and compliance. Kavlen is a complete solution covering all functional areas of real estate investment, development, finance, accounting, management and operations. No more business disruption, downtime, high costs, diminishing ROI, and inflexibility. Run your business your way, break the cycle of technical debt, and focus on high-value, innovative opportunities.</p>
</section>

<section class="abs platform">
  <h2>PLATFORM</h2>
  <span class="rule"></span>
  <div class="eyebrow">STOP SETTLING FOR LESS THAN EXACTLY<br>WHAT YOU WANT</div>
  <p>Kavlen combines the best of all worlds in our Enterprise Applications Platform (EAP): the simplicity and scalability of custom, no-code, software and the security and confidence of a complete, SOC 2 compliant industry solution. Our modular approach enables rapid innovation and re-invention of your business by casting off the shackles of legacy ERP technology and delivering a modern, agile solution that bridges the gaps for all of your real estate workflows.</p>
  <p>No more closed systems, complicated integrations, overreliance on spreadsheets, and complex or unavailable customizations. In their place is Kavlen' robust set of preconfigured yet flexible capabilities that can be deployed as point-solutions or to compose larger business processes.</p>
</section>

<footer>
  <div class="abs footer-col" style="left:142px;width:398px">
    <h4>ABOUT US</h4><span class="rule"></span>
    <p>Kavlen is the real estate industry's modern alternative to rigid, legacy ERP systems. With decades of real estate enterprise software development and implementation expertise — spanning hundreds of blue chip global real estate investment firms — we have a proven track record of enterprise excellence.</p>
  </div>
  <div class="abs footer-col" style="left:622px;width:210px">
    <h4>QUICK LINKS</h4><span class="rule"></span>
    <div class="links"><span>Home</span><span>Resources</span><span>Markets</span><span>About</span><span>Products</span><span>Contact Us</span><span>Platform</span><span></span><span>Services</span></div>
  </div>
  <div class="abs footer-col" style="left:873px;width:190px">
    <h4>CONTACT US</h4><span class="rule"></span>
    <ul class="contact">
      <li><svg width="10" height="13" viewBox="0 0 10 13"><path fill="#e30b13" d="M5 0a5 5 0 015 5c0 3.5-5 8-5 8S0 8.5 0 5a5 5 0 015-5zm0 3a2 2 0 100 4 2 2 0 000-4z"/></svg><span>123, Lorem ipsum dolor sit amet</span></li>
      <li><svg width="11" height="11" viewBox="0 0 24 24"><path fill="#e30b13" d="M6.6 10.8a15 15 0 006.6 6.6l2.2-2.2c.3-.3.7-.4 1-.2 1.1.4 2.3.6 3.6.6.6 0 1 .4 1 1V20c0 .6-.4 1-1 1A17 17 0 013 4c0-.6.4-1 1-1h3.5c.6 0 1 .4 1 1 0 1.3.2 2.5.6 3.6.1.3 0 .7-.2 1z"/></svg><span>+1 888 888 8888</span></li>
      <li><svg width="12" height="10" viewBox="0 0 12 10"><rect width="12" height="10" rx="1" fill="#e30b13"/><path d="M0 0l6 5 6-5" stroke="#161616" fill="none"/></svg><span>info@companyname.com</span></li>
    </ul>
  </div>
  <div class="abs footer-line"></div>
  <div class="abs copyright">Copyright © 2024 Company name - All Rights Reserved</div>
</footer>

</body>
</html>
```